Design website home page for pathology consulting company

Starting a new consulting company with anatomic pathologists focused on expert diagnosis and second opinions on difficult pathology cases. In the near future we will be incorporating next generation diagnostics for rare diseases of childhood into the business. These include discovery and testing of DNA for mutations.

The company is formed around one of the best known pathologists in the world named Marcel "Biscuit" Trowell. The name of the company is "BiscuitLab"

We had a logo design by SketchForum - it is great. I will attach file as soon as I have it (contest ending today). Our company is medical, uses microscopes, DNA, probably will focus on childhood diseases but not solely on childhood diseases. we're not particularly conservative, but the customers we want to appeal to include older practicing pathologists as well as patients (sometimes parents) looking for second opinions.

Think a group of expert doctors diagnosing disease through the microscope and through DNA technology, ages ranging from 35-75 all trained by the best pathologist in the world - "Biscuit"

We receive glass slides from diseases from patients all over the world from docs who need an expert to tell them what is the diagnosis. So "path to the diagnosis" is also part of the company marketing message.

We want the website design to describe our company but be very simple to find what one is looking for as we will use it as the launch page to:
1) order services
2) check results/reports
3) set up new account
4) speak with one of the pathologists
5) see our test menu
6) access our educational material/webinars
Updates

Update - looking for home page design and then finalists will ask for second page design to keep with theme - ok?

Reason: realized this project isn't web design but web home page design - thanks

Reason: Holidays for some in next two weeks

Reason: Hot discussion among collaborators for a few of the submissions. Will provide detail individually this weekend. Thanks so much for all the submissions!

Target Market(s)

Referring pathologists, physicians who want second opinions on pathology disease diagnosis, patients who have had biopsies (either patients themselves or parents of patients), generally high education level

Industry/Entity Type

Marketing

Requirements
Must have
• BiscuitLab
Next Generation Pathology Consultants

```html
<!DOCTYPE html>
<html lang="en">
<head>
<meta charset="utf-8">
<title>BiscuitLab — Next Generation Pathology Consultants</title>
<link rel="stylesheet" href="https://fonts.googleapis.com/css2?family=Open+Sans:wght@400;600;700&family=Roboto+Condensed:wght@700&family=Arimo:wght@400;700&display=swap">
<style>
:root{
  --blue:#1565b0;
  --blue-dark:#0d4c8c;
  --blue-deep:#0b3f76;
  --navy:#123e6c;
  --ink:#222;
  --text:#444;
  --muted:#777;
  --line:#d6d6d6;
  --panel:#f1f1f1;
  --footer:#333;
  --footer-deep:#262626;
  --white:#fff;
}
*{box-sizing:border-box;margin:0;padding:0}
html,body{width:959px;height:1200px;overflow:hidden}
body{position:relative;background:var(--white);font-family:'Arimo',Arial,sans-serif;color:var(--text);font-size:9.5px}
.abs{position:absolute}
.topline{left:0;top:0;width:959px;height:3px;background:var(--blue)}
.account-tab{left:632px;top:0;width:204px;height:22px;background:var(--blue-dark);border-radius:0 0 18px 18px;display:flex;justify-content:center;align-items:center;gap:14px;color:var(--white);font-family:'Open Sans',sans-serif;font-size:9.5px;font-weight:600}
.account-tab span{display:flex;align-items:center;gap:4px}
.brand{left:114px;top:14px;width:140px;text-align:center}
.brand-mark{width:56px;height:56px;border-radius:50%;background:#8c8c8c;margin:0 auto 6px}
.brand-name{font-family:'Open Sans',sans-serif;font-size:20px;font-weight:600;color:var(--navy);line-height:1}
.brand-tag{font-size:7px;color:var(--muted);margin-top:2px}
.talk{left:662px;top:37px;width:162px;height:57px;background:#e4eef7;border:1px solid #b9cfe4}
.talk-head{height:17px;background:var(--blue);color:var(--white);font-family:'Open Sans',sans-serif;font-weight:700;font-size:9.5px;text-align:center;line-height:17px}
.talk-photo{left:0;top:17px;width:38px;height:39px;background:linear-gradient(#d9b79b,#6d8db0)}
.talk-chat{left:40px;top:20px;font-family:'Open Sans',sans-serif;font-size:9.5px;color:#d64a1d;font-weight:600}
.talk-call{left:40px;top:35px;font-family:'Open Sans',sans-serif;font-size:13px;color:var(--navy);font-weight:600}
.nav{left:0;top:104px;width:959px;height:31px;border-top:1px solid #e5e5e5;border-bottom:2px solid var(--blue)}
.nav ul{list-style:none;position:absolute;left:112px;top:0;display:flex;height:29px;align-items:center}
.nav li{font-family:'Open Sans',sans-serif;font-weight:600;font-size:10.5px;color:#555;padding:0 23px;border-left:1px solid #ccc;line-height:12px}
.nav li.home{background:var(--blue);color:var(--white);border:none;height:29px;line-height:29px;padding:0 17px;margin-right:0}
.nav li.home+li{border-left:none;margin-left:6px;border-left:1px solid #ccc}
.hero{left:0;top:135px;width:959px;height:298px;background:linear-gradient(90deg,#cfe4ee 0%,#9fcfe6 30%,#5ea6cd 55%,#c7cfd6 75%,#e9eef2 100%)}
.hero-caption{left:112px;top:382px;height:36px;padding:0 7px;background:rgba(13,76,140,.88);color:var(--white);font-family:'Arimo',Arial,sans-serif;font-weight:700;font-size:21px;line-height:36px;width:290px}
.features{left:0;top:433px;width:959px;height:70px;background:linear-gradient(#1d6fbd,#0d4c8c)}
.feature{position:absolute;top:0;height:70px;border-left:1px solid rgba(255,255,255,.15);color:var(--white);padding:11px 0 0 49px}
.feature.active{background:linear-gradient(#2a80cc,#135fa8)}
.feature h3{font-family:'Open Sans',sans-serif;font-size:12px;font-weight:600;margin-bottom:3px}
.feature p{font-family:'Open Sans',sans-serif;font-size:8.5px;line-height:13px;color:#dce9f5}
.feature svg{position:absolute;left:6px;top:14px}
.welcome{left:114px;top:528px;width:478px}
.welcome h2{font-family:'Open Sans',sans-serif;font-weight:400;font-size:18px;color:var(--ink);padding:0 0 4px 40px;border-bottom:1px dotted #999;position:relative}
.welcome h2 i{position:absolute;left:0;top:-2px;width:31px;height:31px;border-radius:50%;background:#9a9a9a}
.hl{color:var(--blue)}
.welcome .lead{font-weight:700;color:var(--ink);margin:13px 0 6px;font-size:9.5px}
.welcome p{line-height:14.5px;margin-bottom:7px;font-size:9.5px;letter-spacing:.15px}
.more{color:var(--blue);font-weight:700;font-size:9px;text-align:right}
.vdivider{left:609px;top:528px;width:1px;height:178px;background:#e3e3e3}
.quick{left:632px;top:530px;width:216px}
.quick h2{font-family:'Open Sans',sans-serif;font-weight:400;font-size:18px;color:var(--ink);padding-bottom:5px;border-bottom:1px dotted #999;margin-bottom:12px}
.field{height:23px;border:1px solid #d6d6d6;border-radius:2px;background:linear-gradient(#fff,#f1f1f1);font-size:9px;color:#555;padding:5px 6px;margin-bottom:7px;margin-left:2px}
.field.msg{height:40px}
.submit{display:inline-block;margin-left:2px;background:var(--blue-deep);color:var(--white);font-weight:700;font-size:10px;padding:4px 8px;border-radius:2px}
.band{left:0;top:728px;width:959px;height:258px;background:var(--panel);border-top:1px solid #e2e2e2}
.card{position:absolute;top:752px;width:226px;height:210px;background:var(--white);border:1px solid #d5d5d5;border-radius:4px;box-shadow:0 4px 6px rgba(0,0,0,.12);overflow:hidden}
.card-head{height:34px;background:linear-gradient(#1d6fbd,#0d4c8c);color:var(--white);font-family:'Roboto Condensed',sans-serif;font-weight:700;font-size:14.5px;line-height:36px;padding-left:50px;position:relative}
.card-head i{position:absolute;left:9px;top:6px;width:32px;height:32px;border-radius:50%;background:var(--white);border:2px solid var(--blue-dark)}
.card-img{margin:11px 9px 6px;height:94px}
.card p{font-size:9.5px;line-height:13.5px;padding:0 9px}
.card p b{color:var(--ink)}
.card .more{padding:2px 9px 0}
.news{padding:10px 9px 0}
.news-item{display:flex;gap:5px;padding-bottom:6px;margin-bottom:7px;border-bottom:1px solid #e3e3e3;font-size:9.5px;line-height:12.5px}
.news-item:last-child{border:none;margin-bottom:0}
.date{flex:none;width:21px;height:22px;background:#444;color:var(--white);font-size:7.5px;text-align:center;line-height:9px;padding-top:2px;border-radius:2px;margin-top:2px}
.news-item .t{color:var(--ink)}
.footer{left:0;top:986px;width:959px;height:186px;background:radial-gradient(circle at 50% 40%,#3d3d3d,#2c2c2c)}
.copy{left:0;top:1172px;width:959px;height:28px;background:#1f1f1f;color:#ddd;font-size:9px;line-height:28px;padding-left:114px}
.fh{font-family:'Open Sans',sans-serif;font-size:14px;color:#eee;padding-bottom:6px;border-bottom:1px dotted #555}
.testi{left:114px;top:998px;width:200px}
.arrows{position:absolute;right:0;top:3px;display:flex;gap:3px}
.arrows span{width:13px;height:13px;border-radius:50%;background:#ddd}
.quote{margin-top:12px;background:var(--white);border-radius:4px;padding:8px 9px;font-style:italic;font-size:9px;line-height:13.5px;color:#444;position:relative;letter-spacing:.3px}
.quote:after{content:"";position:absolute;left:24px;bottom:-10px;border-left:10px solid var(--white);border-bottom:10px solid transparent}
.quote b{font-size:20px;color:#777;font-style:normal;line-height:0;vertical-align:-6px;margin-right:3px}
.author{margin:11px 0 0 41px;font-size:9px;line-height:11px;color:#eee}
.author span{color:#4fa0e6;display:block}
.links{left:363px;top:998px;width:118px}
.links ul{list-style:none;margin-top:6px}
.links li{color:#ddd;font-size:9px;line-height:19.5px;padding-left:12px;position:relative}
.links li:before{content:"›";position:absolute;left:0;color:#aaa}
.contact{left:513px;top:998px;width:140px}
.ci{display:flex;gap:8px;color:#ddd;font-size:9px;line-height:13.5px;margin-top:10px}
.ci svg{flex:none;margin-top:1px}
.fbrand{left:714px;top:1010px;width:132px;text-align:center}
.fbrand .brand-mark{width:64px;height:64px;background:#777}
.fbrand .brand-name{color:#bbb}
.fbrand .brand-tag{color:#999}
.social{display:flex;gap:6px;justify-content:center;margin-top:10px}
.social span{width:20px;height:20px;border-radius:50%;background:#ddd;border:2px solid #555}
</style>
</head>
<body>
<div class="abs topline"></div>
<div class="abs account-tab">
  <span><svg width="11" height="11" viewBox="0 0 12 12"><circle cx="6" cy="3.5" r="3" fill="#fff"/><path d="M0 12c0-4 3-5.5 6-5.5S12 8 12 12z" fill="#fff"/></svg>Create Account</span>
  <span><svg width="9" height="11" viewBox="0 0 10 12"><rect x="0" y="5" width="10" height="7" fill="#fff"/><path d="M2.5 5V3.5a2.5 2.5 0 0 1 5 0V5" stroke="#fff" stroke-width="1.5" fill="none"/></svg>Login</span>
</div>

<div class="abs brand">
  <div class="brand-mark"></div>
  <div class="brand-name">BiscuitLab</div>
  <div class="brand-tag">Next Generation Pathology Consultants</div>
</div>

<div class="abs talk">
  <div class="talk-head">SPEAK WITH PATHOLOGISTS</div>
  <div class="abs talk-photo" role="img" aria-label="Photo of a support pathologist with headset"></div>
  <div class="abs talk-chat">Click Here For Live Chat</div>
  <div class="abs talk-call">Call-555-018-2040</div>
</div>

<nav class="abs nav">
  <ul>
    <li class="home">HOME</li><li>ABOUT</li><li>SERVICES</li><li>EDUCATION</li><li>NEW ACCOUNT</li><li>ASK QUESTIONS</li><li>CONTACT US</li>
  </ul>
</nav>

<div class="abs hero" role="img" aria-label="Photo of a pathologist looking into a microscope beside a monitor in a blue-lit lab"></div>
<div class="abs hero-caption">PATH TO THE DIAGNOSIS</div>

<div class="abs features">
  <div class="feature" style="left:112px;width:174px">
    <svg width="38" height="38" viewBox="0 0 38 38" fill="#fff"><circle cx="13" cy="24" r="8"/><circle cx="13" cy="24" r="3" fill="#15599e"/><circle cx="27" cy="11" r="6"/><circle cx="27" cy="11" r="2" fill="#15599e"/></svg>
    <h3>Order Services</h3><p>Lorem Ipsum is simpl ummy<br>text of printing atypeset...</p>
  </div>
  <div class="feature active" style="left:286px;width:186px;padding-left:57px">
    <svg width="42" height="40" viewBox="0 0 42 40" fill="#fff"><path d="M6 3h20l6 6v26H6z"/><rect x="10" y="13" width="16" height="2" fill="#1d6fbd"/><rect x="10" y="18" width="12" height="2" fill="#1d6fbd"/><circle cx="30" cy="28" r="9" stroke="#1d6fbd" stroke-width="2"/><path d="M25 28l4 4 6-7" stroke="#1d6fbd" stroke-width="2.5" fill="none"/></svg>
    <h3>Check Reports</h3><p>Lorem Ipsum is simpl ummy<br>text of printing atypeset...</p>
  </div>
  <div class="feature" style="left:472px;width:194px;padding-left:58px">
    <svg width="40" height="40" viewBox="0 0 40 40" fill="#fff"><rect x="2" y="4" width="8" height="32"/><rect x="13" y="4" width="8" height="32"/><path d="M24 8l7-2 7 28-7 2z"/></svg>
    <h3>Educational Material</h3><p>Lorem Ipsum is simpl ummy<br>text of printing atypeset...</p>
  </div>
  <div class="feature" style="left:666px;width:180px;padding-left:59px">
    <svg width="40" height="40" viewBox="0 0 40 40" fill="#fff"><rect x="12" y="1" width="14" height="3"/><path d="M15 4h8v12l12 20H3l12-20z"/></svg>
    <h3>Our Test Menu</h3><p>Lorem Ipsum is simpl ummy<br>text of printing atypeset...</p>
  </div>
</div>

<section class="abs welcome">
  <h2><i></i>WELCOME TO <span class="hl">BISCUITLAB</span></h2>
  <p class="lead">Lorem ipsum dolor sit amet, consectetuer adipiscing elit,</p>
  <p>Sed diam nonummy nibh euismod tincidunt ut laoreet dolore magna aliquam erat volutpat. Ut wisi eniminti veniam, quis nostrud exerci tation ullamcorper suscipit lobortis nisl ut aliquip ex ea commodo consequat.</p>
  <p>Ut wisi enim ad minim veniam, quis nostrud exerci tation ullamcorper suscipit lobortis nisl ut aliquip comm consequat. Duis autem vel eum iriure dolor in hendrerit in vulputate velit esse molestie consequat, vel ill dolore eu feugiat nulla facilisis at vero eros et accumsan et iusto odio dignissim qui blandit praesent luptatumdeelenit augue duis dolore te feugait nulla facilisi.</p>
  <div class="more">Read more »</div>
</section>
<div class="abs vdivider"></div>
<section class="abs quick">
  <h2>QUICK <span class="hl">CONTACT</span></h2>
  <div class="field">Name</div>
  <div class="field">Email</div>
  <div class="field msg">Message</div>
  <span class="submit">SUBMIT</span>
</section>

<div class="abs band"></div>
<article class="card" style="left:114px">
  <div class="card-head"><i></i>WHY BISCUITLAB</div>
  <div class="card-img" role="img" aria-label="Photo of lab scientists working with microscopes and flasks" style="background:linear-gradient(135deg,#c9dbe6,#7fa4bf 60%,#e8e1d8)"></div>
  <p><b>Lorem ipsum</b> sit amet consectetur adipisicinge elitsed do eiusmod tempor incididunt ut laborei et dolore magna aliqua Ut enim ad minim amie.</p>
  <div class="more">Read more »</div>
</article>
<article class="card" style="left:367px">
  <div class="card-head"><i></i>EXPERT DIAGNOSIS</div>
  <div class="card-img" role="img" aria-label="Photo of a researcher at a microscope in a busy lab" style="background:linear-gradient(135deg,#3f3a3a,#3a5f9c 55%,#a7b4c4)"></div>
  <p><b>Lorem ipsum</b> sit amet consectetur adipisicinge elitsed do eiusmod tempor incididunt ut laborei et dolore magna aliqua Ut enim ad minim amie.</p>
  <div class="more">Read more »</div>
</article>
<article class="card" style="left:622px">
  <div class="card-head"><i></i>LATEST NEWS</div>
  <div class="news">
    <div class="news-item"><div class="date">23<br>Aug</div><div><span class="t">Ut wisi enim ad minim veniam..</span><br>Lorem ipsum sit amet consectetur adipisic elitsed do eiUt enim ad minim amie venia</div></div>
    <div class="news-item"><div class="date">23<br>Aug</div><div><span class="t">Ut wisi enim ad minim veniam..</span><br>Lorem ipsum sit amet consectetur adipisic elitsed do eiUt enim ad minim amie venia</div></div>
    <div class="news-item"><div class="date">23<br>Aug</div><div><span class="t">Ut wisi enim ad minim veniam..</span><br>Lorem ipsum sit amet consectetur adipisic elitsed do eiUt enim ad minim amie venia</div></div>
  </div>
  <div class="more">Read more »</div>
</article>

<footer class="abs footer"></footer>
<div class="abs testi">
  <div class="fh">Client Testimonial</div>
  <div class="arrows"><span></span><span></span></div>
  <div class="quote"><b>“</b>Sed diam nonummy nibh euismod tincidunt ut laoreet dolore magna aliquam erat volutpat. Ut wisi eniminti veniam, quis nostrud exerci tation ullamcorper suscipit lobortis nisl ut aliquip ex ea commodo consequat.</div>
  <div class="author"><span>Dr. Alden Marsh Corwell, M.D</span>Medical Director</div>
</div>
<div class="abs links">
  <div class="fh">Quick Links</div>
  <ul><li>Home</li><li>About</li><li>Services</li><li>Education</li><li>New Account</li><li>Ask Questions</li><li>Contact Us</li></ul>
</div>
<div class="abs contact">
  <div class="fh">Contact Us</div>
  <div class="ci"><svg width="10" height="13" viewBox="0 0 10 13"><path d="M5 0a5 5 0 0 1 5 5c0 3-5 8-5 8S0 8 0 5a5 5 0 0 1 5-5z" fill="#fff"/><circle cx="5" cy="5" r="1.8" fill="#333"/></svg><div>Lorem ipsum dolor sit amet consectetuer adipiscing elit,</div></div>
  <div class="ci"><svg width="11" height="11" viewBox="0 0 12 12"><path d="M2 0l3 3-1.5 2c1 2 2 3 3.5 3.5L9 7l3 3-2 2C5 12 0 7 0 2z" fill="#fff"/></svg><div>Toll Free: 555-018-2040<br>Telephone: 555-018-2040</div></div>
  <div class="ci"><svg width="11" height="11" viewBox="0 0 12 12" fill="#fff"><rect x="3" y="0" width="6" height="3"/><rect x="0" y="4" width="12" height="5"/><rect x="3" y="8" width="6" height="4"/></svg><div>Fax: 555-018-2040</div></div>
  <div class="ci"><svg width="11" height="9" viewBox="0 0 12 9"><rect width="12" height="9" fill="#fff"/><path d="M0 0l6 5 6-5" stroke="#333" fill="none"/></svg><div>info@biscuitlab.example</div></div>
</div>
<div class="abs fbrand">
  <div class="brand-mark"></div>
  <div class="brand-name">BiscuitLab</div>
  <div class="brand-tag">Next Generation Pathology Consultants</div>
  <div class="social"><span></span><span></span><span></span><span></span></div>
</div>
<div class="abs copy">Copyright © 2013 BiscuitLab . All Rights Reserved.</div>
</body>
</html>
```